Marlowby Services Website Design

We have most content but require a professional design. We have a logo already and will need it utilized along with several of the photos from the attached documentation.
First page should have our mission and Vision and the synapsis provided in the word document. Visitors will be prompted to select from one of our 3 divisions from this page.
Each division will have the same list of tabs : About, Services, Safety, Careers and Contact.
Photos on each divisions page should be representative of the divisions offerings. The word doc attached contains the requested content and we are open to edits that would complement and fill the website.
I like the Quorvane site www.quorvane.example - they are our competition so cant be modeled directly after this.
Please include prompts to request quote at each service page. align the format of the geotechnical page to the other 2 divisions.
I used chat gpt for some of the content so will need it optimized for SCO.

```html
<!DOCTYPE html>
<html lang="en">
<head>
<meta charset="utf-8">
<title>Marlowby Services</title>
<link rel="stylesheet" href="https://fonts.googleapis.com/css2?family=Poppins:wght@400;500;600;700;800&display=swap">
<style>
:root{
  --red:#ed1f26;
  --dark:#2b2b2b;
  --ink:#222;
  --white:#fff;
  --pink:#f6e8ec;
  --grey:#e4e4e4;
  --earth-a:#6b5a46;
  --earth-b:#3f3428;
}
*{box-sizing:border-box;margin:0;padding:0}
html,body{width:1200px;height:3371px;overflow:hidden}
body{position:relative;font-family:'Poppins',sans-serif;color:var(--ink);background:var(--white)}
.abs{position:absolute}
.btn{position:absolute;background:var(--red);color:var(--white);font-weight:700;font-size:15px;display:flex;align-items:center;justify-content:center;letter-spacing:-.2px;border-radius:2px}
.brand{font-family:'Poppins',sans-serif;font-weight:800;letter-spacing:5px;text-transform:uppercase;line-height:1}

/* hero */
.hero{position:absolute;left:0;top:0;width:1200px;height:780px;overflow:hidden}
.hero-photo{position:absolute;inset:0;background:linear-gradient(180deg,#5c6a4f 0%,var(--earth-a) 35%,var(--earth-b) 100%)}
.hero-shape{position:absolute;left:0;top:0}
.nav{position:absolute;top:0;left:0;width:1200px;height:100px}
.nav .logo{position:absolute;left:111px;top:38px;color:var(--white);font-size:36px}
.nav a{position:absolute;top:40px;color:var(--white);text-decoration:none;font-size:16.5px;font-weight:600}
.nav a.active{color:var(--red)}
.nav .cta{top:26px;left:945px;width:142px;height:46px}
.connect{position:absolute;left:22px;top:210px;width:24px}
.social-dot{width:20px;height:20px;border-radius:50%;background:var(--white);margin:0 auto 22px}
.connect .rule{width:1px;height:82px;background:var(--white);margin:0 auto}
.connect .label{position:absolute;left:-26px;top:212px;transform:rotate(-90deg);color:var(--white);font-size:15px;letter-spacing:1px;font-weight:500;width:80px}
.hero .wordmark{position:absolute;right:126px;top:508px;color:var(--white);font-size:44px}
.hero .start{left:930px;top:588px;width:144px;height:47px}
.dots{position:absolute;left:569px;top:621px;display:flex;gap:7px;align-items:center}
.dots span{width:10px;height:10px;border:1px solid var(--white);border-radius:50%}
.dots span.on{width:14px;height:14px;background:var(--red);border:2px solid var(--white)}

/* services */
.intro-frame{left:113px;top:856px;width:481px;height:468px;background:var(--red)}
.intro-photo{left:123px;top:866px;width:461px;height:448px;background:linear-gradient(180deg,#9aa2a0,#7c7a6c 60%,#6d6a5e)}
.h2{font-weight:800;font-size:39px;color:var(--red);text-transform:uppercase;line-height:1.1;position:absolute}
.rule-red{position:absolute;height:3px;background:var(--red)}
.intro-title{left:626px;top:975px}
.intro-text{left:626px;top:1050px;width:449px;font-size:19.5px;line-height:31px;text-align:justify}
.intro .quote{left:626px;top:1178px;width:144px;height:47px}

/* vision */
.vision{left:0;top:1424px;width:1200px;height:290px;background:var(--red);color:var(--white);text-align:center}
.vision h2{position:absolute;left:0;width:100%;top:72px;font-size:39px;font-weight:800}
.vision .rule-white{position:absolute;left:493px;top:128px;width:214px;height:3px;background:var(--white)}
.vision p{position:absolute;left:130px;width:940px;top:150px;font-size:19.5px;line-height:31px}

/* mission */
.mission-band{left:0;top:1850px;width:1200px;height:377px;background:var(--pink)}
.mission-block{left:641px;top:1822px;width:466px;height:471px;background:var(--red)}
.mission-photo{left:658px;top:1802px;width:466px;height:471px;background:linear-gradient(180deg,#7f9a5a 0%,#5d7742 45%,#76736a 70%,#5f5b54 100%)}
.mission-title{right:578px;top:1890px;text-align:right}
.mission-text{left:113px;top:1982px;width:509px;font-size:16.5px;line-height:24.8px;text-align:justify;text-align-last:right;color:#333}

/* divisions */
.div-title{left:0;width:1200px;text-align:center;top:2370px}
.card{position:absolute;top:2464px;width:308px;height:349px;border:3px solid transparent}
.card.active{border-color:var(--red)}
.card .photo{position:absolute;left:-3px;top:-3px;width:308px;height:235px;border:3px solid var(--red)}
.card h3{position:absolute;left:0;width:100%;top:248px;text-align:center;font-size:23px;font-weight:700;line-height:30px;color:#2a2a2a;text-transform:uppercase}
.card .rule-red{left:107px;top:322px;width:94px}

/* footer */
.footer-shape{position:absolute;left:0;top:2890px}
.footer{left:0;top:3010px;width:1200px;height:361px;background:var(--dark);color:var(--white)}
.footer .logo{position:absolute;left:187px;top:108px;color:var(--red);font-size:38px}
.footer .socials{position:absolute;left:286px;top:166px;display:flex;gap:28px}
.footer .socials span{width:20px;height:20px;border-radius:50%;background:var(--white)}
.fcol{position:absolute;top:63px}
.fcol h4{font-size:18px;font-weight:600;line-height:26px}
.fcol .u{width:44px;height:2px;background:var(--red);margin:4px 0 8px}
.fcol li{list-style:none;font-size:12.5px;line-height:23.3px}
.footer .divider{position:absolute;left:110px;top:277px;width:976px;height:1px;background:var(--red)}
.footer .copy{position:absolute;left:0;width:1200px;text-align:center;top:308px;font-size:14px}
</style>
</head>
<body>

<header class="hero">
  <div class="hero-photo" role="img" aria-label="Photo of a white aerial lift truck with extended boom parked on a dirt lot"></div>
  <svg class="hero-shape" width="1200" height="780" viewBox="0 0 1200 780">
    <polygon points="0,628 1200,726 1200,780 0,780" fill="#fff"/>
    <polygon points="0,628 1200,726 1200,749 0,648" fill="var(--grey)"/>
    <polygon points="0,648 356,677 0,775" fill="var(--red)"/>
  </svg>
  <nav class="nav">
    <div class="logo brand">Marlowby</div>
    <a class="active" style="left:486px">Home</a>
    <a style="left:574px">About</a>
    <a style="left:663px">Services</a>
    <a style="left:770px">Safety</a>
    <a style="left:861px">Careers</a>
    <span class="btn cta">CONTACT US</span>
  </nav>
  <div class="connect">
    <div class="social-dot" aria-label="Social link"></div>
    <div class="social-dot" aria-label="Social link"></div>
    <div class="rule"></div>
    <div class="label">CONNECT</div>
  </div>
  <div class="wordmark brand">Marlowby</div>
  <div class="dots"><span></span><span></span><span class="on"></span><span></span></div>
  <span class="btn start">GET STARTED</span>
</header>

<section class="intro">
  <div class="abs intro-frame"></div>
  <div class="abs intro-photo" role="img" aria-label="Worker in an aerial lift bucket with a for-hire sign above a small town"></div>
  <h2 class="h2 intro-title">Marlowby Services</h2>
  <div class="rule-red" style="left:626px;top:1030px;width:175px"></div>
  <p class="abs intro-text">Delivering safe, reliable aerial access and maintenance services to Oil&amp;Gas, Construction, Utility, &amp; Renewable energy industries.</p>
  <span class="btn quote">REQUEST QUOTES</span>
</section>

<section class="abs vision">
  <h2>OUR VISION</h2>
  <div class="rule-white"></div>
  <p>To be the leading provider of aerial access, geotechnical drilling, and service solutions, setting the standard for excellence in safety, efficiency, and environmental stewardship.</p>
</section>

<section class="mission">
  <div class="abs mission-band"></div>
  <div class="abs mission-block"></div>
  <div class="abs mission-photo" role="img" aria-label="Aerial lift truck parked on a gravel lot in front of green trees"></div>
  <h2 class="h2 mission-title">Mission Statement</h2>
  <div class="rule-red" style="left:408px;top:1947px;width:214px"></div>
  <p class="abs mission-text">At Marlowby, our mission is to deliver unparalleled aerial access, geotechnical drilling, and service and maintenance solutions, consistently exceeding our clients' expectations. We strive to achieve this by investing in cutting-edge technology, fostering a culture of safety and continuous improvement, and prioritizing environmental sustainability. Through collaboration, integrity, and dedication, we aim to contribute to the success of our clients while maintaining the highest standards of quality and professionalism.</p>
</section>

<section class="divisions">
  <h2 class="h2 div-title">Select Division</h2>
  <div class="rule-red" style="left:494px;top:2427px;width:212px"></div>
  <div class="card active" style="left:113px">
    <div class="photo" role="img" aria-label="Aerial lift boom raised beside a tall white tower under blue sky" style="background:linear-gradient(180deg,#3f79c9 0%,#7fa6d8 70%,#6d7a55 100%)"></div>
    <h3>Aerial<br>Access</h3>
    <div class="rule-red"></div>
  </div>
  <div class="card" style="left:446px">
    <div class="photo" role="img" aria-label="Overhead view of a white drilling truck on bare ground" style="background:linear-gradient(135deg,#4a3f33,#7a6a55 50%,#5a4c3d)"></div>
    <h3>Geotechnical<br>Drilling</h3>
    <div class="rule-red"></div>
  </div>
  <div class="card" style="left:780px">
    <div class="photo" role="img" aria-label="Two white service trucks with booms parked on a gravel yard" style="background:linear-gradient(180deg,#b9bec4 0%,#9a9d9c 55%,#77756f 100%)"></div>
    <h3>Renewable Energy<br>Services</h3>
    <div class="rule-red"></div>
  </div>
</section>

<svg class="footer-shape" width="1200" height="130" viewBox="0 0 1200 130">
  <polygon points="0,12 1200,98 1200,130 0,130" fill="var(--grey)"/>
  <polygon points="0,30 1200,118 1200,130 0,130" fill="var(--dark)"/>
  <polygon points="916,94 1200,18 1200,120" fill="var(--red)"/>
</svg>
<footer class="abs footer">
  <div class="logo brand">Marlowby</div>
  <div class="socials"><span aria-label="Social link"></span><span aria-label="Social link"></span></div>
  <div class="fcol" style="left:540px">
    <h4>Quick Links</h4><div class="u"></div>
    <ul><li>Home</li><li>About</li><li>Services</li><li>Safety</li><li>Careers</li><li>Contact Us</li></ul>
  </div>
  <div class="fcol" style="left:739px">
    <h4>Links</h4><div class="u"></div>
    <ul><li>Copyright</li><li>Terms of Use</li><li>Privacy Policy</li><li>Accessibility</li><li>Sitemap</li></ul>
  </div>
  <div class="fcol" style="left:899px">
    <h4>Support</h4><div class="u"></div>
    <ul><li>Team</li><li>About Us</li><li>Careers</li><li>Our Values</li><li>Data Security</li></ul>
  </div>
  <div class="divider"></div>
  <div class="copy">©2024. All rights reserved.</div>
</footer>

</body>
</html>
```